Garlic Farm for Farm Sales/Restaurant sales

Need a professional, but appealing to agriculture world. We are selling 27 kinds of Organic Garlic from a farm in Simla,CO. I have uploaded logo and business information-we are going to need a template, because I will need to use it for four separate people.
-We are trying to appeal to Farm to table restaurants
-As well as growers/farmers

Target Market(s)

Agriculture Sales/Restaurants-Organic

Industry/Entity Type

Agriculture

Contact Information for Business Card

Want it to look more unique then your average kelto stock card- I want it to look amazing

Font styles to use
Sans Serif

Colors
0455a3
ec1f27
fbed22
ffffff

Requirements
Must have
• Just be creative
Nice to have
• Colorful
Should not have
• plain

```html
<!DOCTYPE html>
<html lang="en">
<head>
<meta charset="utf-8">
<title>Ridge Bulb Garlic – Business Card</title>
<link rel="stylesheet" href="https://fonts.googleapis.com/css2?family=Open+Sans:wght@400;600;700&display=swap">
<style>
  :root {
    --navy: #1c2f5c;
    --red: #c8202a;
    --yellow: #fbe122;
    --white: #ffffff;
    --backdrop: #e6e3de;
  }
  * { margin: 0; padding: 0; box-sizing: border-box; }
  html, body {
    width: 1200px; height: 902px; overflow: hidden;
    background: var(--backdrop);
    font-family: "Open Sans", Arial, sans-serif;
  }
  .card {
    position: absolute; left: 130px; top: 182px;
    width: 940px; height: 537px;
    border-radius: 26px; overflow: hidden;
    background: var(--white);
    box-shadow: 0 10px 30px rgba(0,0,0,0.18);
  }
  .card-shapes { position: absolute; inset: 0; }
  .name-marker {
    position: absolute; left: -24px; top: 76px;
    width: 48px; height: 48px; border-radius: 50%;
    background: var(--yellow);
  }
  .holder-name {
    position: absolute; left: 50px; top: 78px;
    color: var(--white); font-size: 31px; font-weight: 600;
    letter-spacing: 0.3px;
  }
  .address {
    position: absolute; left: 52px; top: 210px;
    color: var(--white); font-size: 23px; line-height: 32px;
    letter-spacing: 0.6px;
  }
  .contact-list {
    position: absolute; left: 52px; top: 302px; list-style: none;
  }
  .contact-item {
    display: flex; align-items: center; gap: 12px;
    height: 33px; color: var(--white); font-size: 24px;
    letter-spacing: 0.3px;
  }
  .contact-icon {
    width: 26px; height: 26px; border-radius: 4px;
    background: var(--yellow); display: flex;
    align-items: center; justify-content: center;
  }
  .social-row {
    position: absolute; left: 52px; top: 422px;
    display: flex; gap: 10px;
  }
  .social-square {
    width: 33px; height: 33px; border-radius: 3px;
    background: var(--yellow);
  }
  .brand {
    position: absolute; left: 487px; right: 0; top: 110px;
    display: flex; flex-direction: column; align-items: center; gap: 26px;
  }
  .brand-dot {
    width: 150px; height: 150px; border-radius: 50%;
    background: var(--red);
  }
  .brand-name {
    color: var(--navy); font-size: 50px; font-weight: 700;
    letter-spacing: 0.5px;
  }
</style>
</head>
<body>
  <div class="card">
    <svg class="card-shapes" width="940" height="537" viewBox="0 0 940 537" aria-hidden="true">
      <rect class="panel-navy" x="0" y="0" width="500" height="537" fill="var(--navy)"/>
      <path class="divider-red" d="M487 0 Q 400 268 487 537 L 500 537 L 500 0 Z" fill="var(--red)"/>
      <path class="panel-white" d="M487 0 Q 418 268 487 537 L 940 537 L 940 0 Z" fill="var(--white)"/>
    </svg>

    <span class="name-marker"></span>
    <h1 class="holder-name">Dana Holt</h1>

    <p class="address">P.O. Box 12 Larkin,<br>CO&nbsp; 80000</p>

    <ul class="contact-list">
      <li class="contact-item">
        <span class="contact-icon">
          <svg width="16" height="16" viewBox="0 0 16 16"><path d="M3 1.5 L6 1.5 L7 5 L5.2 6.3 Q6.5 9.5 9.7 10.8 L11 9 L14.5 10 L14.5 13 Q14.5 14.5 13 14.5 Q2 13.5 1.5 3 Q1.5 1.5 3 1.5 Z" fill="var(--navy)"/></svg>
        </span>
        555-010-4827
      </li>
      <li class="contact-item">
        <span class="contact-icon">
          <svg width="18" height="14" viewBox="0 0 18 14"><rect x="1" y="1" width="16" height="12" fill="var(--navy)"/><path d="M1.5 1.5 L9 8 L16.5 1.5" stroke="var(--yellow)" stroke-width="1.5" fill="none"/></svg>
        </span>
        Dana@RidgeBulb.com
      </li>
      <li class="contact-item">
        <span class="contact-icon">
          <svg width="18" height="18" viewBox="0 0 18 18" fill="none" stroke="var(--navy)" stroke-width="1.4"><circle cx="9" cy="9" r="7.5"/><ellipse cx="9" cy="9" rx="3.2" ry="7.5"/><line x1="1.5" y1="9" x2="16.5" y2="9"/><line x1="2.8" y1="5" x2="15.2" y2="5"/><line x1="2.8" y1="13" x2="15.2" y2="13"/></svg>
        </span>
        RidgeBulb.com
      </li>
    </ul>

    <div class="social-row" aria-label="Social profiles">
      <span class="social-square"></span>
      <span class="social-square"></span>
      <span class="social-square"></span>
      <span class="social-square"></span>
    </div>

    <div class="brand">
      <span class="brand-dot"></span>
      <p class="brand-name">Ridge Bulb Garlic</p>
    </div>
  </div>
</body>
</html>
```